BildeVOLD buisnesscard

Hey :) I need a modern buisnesscard for my company BildeVOLD
It most have:
Dagligleder og Fotograf: Henrik Audun Strandvik

Mob: +4791264085
Epost: post@bildevold.example
Adresse: Kvernbakken9, 6040 Langevåg

Facbook and instagram logo with text BildeVOLD

BildeVOLD logo

It Company

```html
<!DOCTYPE html>
<html lang="no">
<head>
<meta charset="utf-8">
<title>BildeVOLD – visittkort</title>
<link href="https://fonts.googleapis.com/css2?family=Noto+Sans:wght@400;700&display=swap" rel="stylesheet">
<style>
  :root {
    --backdrop: #7a5236;
    --card-silver: #a9aaa9;
    --card-dark: #262626;
    --ink-light: #a6a7a6;
    --ink-dark: #2a2a2a;
    --bracket: #c9c9c9;
  }
  * { margin: 0; padding: 0; box-sizing: border-box; }
  html, body { width: 1200px; height: 1200px; overflow: hidden; }
  body {
    background: var(--backdrop);
    font-family: "Noto Sans", Verdana, sans-serif;
    position: relative;
  }
  .card { position: absolute; width: 722px; height: 435px; }

  /* Front */
  .card-front { left: 240px; top: 106px; background: var(--card-silver); }
  .front-panel {
    position: absolute; left: 24px; top: 24px; width: 677px; height: 340px;
    background: var(--card-dark);
  }
  .frame-corner { position: absolute; width: 39px; height: 39px; border-color: var(--bracket); border-style: solid; border-width: 0; }
  .corner-tl { left: 14px; top: 16px; border-top-width: 1.5px; border-left-width: 1.5px; }
  .corner-tr { right: 14px; top: 16px; border-top-width: 1.5px; border-right-width: 1.5px; }
  .corner-bl { left: 14px; bottom: 18px; border-bottom-width: 1.5px; border-left-width: 1.5px; }
  .corner-br { right: 14px; bottom: 18px; border-bottom-width: 1.5px; border-right-width: 1.5px; }
  .identity {
    position: absolute; left: 0; right: 0; top: 120px; text-align: center; color: var(--ink-light);
  }
  .person-name { font-size: 26px; font-weight: 400; letter-spacing: 0.3px; line-height: 34px; }
  .divider-dot { display: block; margin: 6px auto 2px; }
  .person-role { font-size: 17px; line-height: 22px; letter-spacing: 0.3px; }
  .contact {
    position: absolute; left: 0; right: 0; top: 380px; text-align: center;
    color: var(--ink-dark); font-size: 16.5px; line-height: 21.5px; letter-spacing: 0.2px;
  }

  /* Back */
  .card-back { left: 238px; top: 624px; background: var(--card-dark); }
  .brand-name {
    position: absolute; left: 0; right: 0; top: 232px; text-align: center;
    color: var(--ink-light); font-size: 50px; font-weight: 700; line-height: 60px;
  }
  .social {
    position: absolute; left: 0; right: 0; top: 334px;
    display: flex; justify-content: center; gap: 22px;
    color: var(--ink-light); font-size: 19px;
  }
  .social-item { display: flex; align-items: center; gap: 14px; }
  .social-mark { width: 32px; height: 32px; border: 2px solid var(--ink-light); border-radius: 50%; }
</style>
</head>
<body>
  <section class="card card-front">
    <div class="front-panel">
      <span class="frame-corner corner-tl"></span>
      <span class="frame-corner corner-tr"></span>
      <span class="frame-corner corner-bl"></span>
      <span class="frame-corner corner-br"></span>
      <div class="identity">
        <h1 class="person-name">Henrik Audun Strandvik</h1>
        <svg class="divider-dot" width="18" height="18" viewBox="0 0 18 18" aria-hidden="true">
          <circle cx="9" cy="9" r="7.5" fill="none" stroke="#a6a7a6" stroke-width="1.3"/>
          <circle cx="9" cy="9" r="4" fill="none" stroke="#a6a7a6" stroke-width="1.3"/>
        </svg>
        <p class="person-role">Dagligleder og Fotograf</p>
      </div>
    </div>
    <p class="contact">
      M: 479 126 4085 | www.bildevold.example | post@bildevold.example<br>
      Kvernbakken9, 6040 Langevåg
    </p>
  </section>

  <section class="card card-back">
    <p class="brand-name">BildeVOLD</p>
    <div class="social">
      <span class="social-item"><span class="social-mark"></span>BildeVOLD</span>
      <span class="social-item"><span class="social-mark"></span>BildeVOLD</span>
    </div>
  </section>
</body>
</html>
```